Retail Seafood business needs package/label design

In need of packaging/label design for multiple seafood products such as sword fish, halibut, cod fish, scallops, mahi, catfish, and lobster tails

```html
<!DOCTYPE html>
<html lang="en">
<head>
<meta charset="utf-8">
<title>Harbor Pantry – Yellowfin Tuna Label</title>
<link href="https://fonts.googleapis.com/css2?family=Oswald:wght@300;400;500&family=Caveat:wght@500&family=Josefin+Sans:wght@400;600&display=swap" rel="stylesheet">
<style>
  :root {
    --page-bg: #e6fbf6;
    --label-light: #b9d9dc;
    --navy: #3f4e78;
    --sea-teal: #3e8790;
    --strip-teal: #66aab4;
    --script-teal: #3a8a91;
    --cream: #efe8dc;
    --rule: #7fa9b3;
  }
  * { margin: 0; padding: 0; box-sizing: border-box; }
  html, body { width: 1200px; height: 728px; overflow: hidden; background: var(--page-bg); }
  .canvas { position: relative; width: 1200px; height: 728px; }

  .label {
    position: absolute; left: 445px; top: 0; width: 309px; height: 728px;
    background: var(--label-light); overflow: hidden;
  }
  .brand-block {
    position: absolute; left: 93px; top: 0; width: 122px; height: 110px;
    background: var(--navy); display: flex; align-items: center; justify-content: center;
  }
  .brand-name {
    font-family: "Josefin Sans", sans-serif; font-weight: 600; color: var(--cream);
    text-align: center; line-height: 1.05;
  }
  .brand-block .brand-name { font-size: 17px; margin-top: 14px; }

  .tagline {
    position: absolute; top: 129px; width: 100%; text-align: center;
    font-family: "Oswald", sans-serif; font-weight: 400; font-size: 7.5px;
    letter-spacing: 1.6px; line-height: 8.3px; color: var(--navy);
  }

  .rule { position: absolute; left: 0; width: 100%; height: 1px; background: var(--rule); }
  .rule-v { position: absolute; top: 201px; height: 142px; width: 1px; background: var(--rule); }

  .side-note {
    position: absolute; top: 272px; font-family: "Josefin Sans", sans-serif;
    font-size: 7px; letter-spacing: 1.4px; color: var(--navy); white-space: nowrap;
    transform: translate(-50%, -50%) rotate(-90deg);
  }

  .product-title {
    position: absolute; left: 59px; top: 214px; width: 197px; text-align: center;
    font-family: "Oswald", sans-serif; font-weight: 500; font-size: 44px;
    line-height: 40px; color: var(--navy); transform: scaleX(0.86);
  }
  .product-script {
    position: absolute; left: 59px; top: 290px; width: 197px; text-align: center;
    font-family: "Caveat", cursive; font-size: 30px; color: var(--script-teal);
  }
  .claim, .pricing {
    position: absolute; width: 100%; text-align: center; font-family: "Josefin Sans", sans-serif;
  }
  .claim { top: 347px; font-size: 7.5px; letter-spacing: 1px; color: var(--script-teal); }
  .pricing { top: 367px; font-size: 6px; letter-spacing: 0.9px; color: var(--navy); font-weight: 600; }

  .sea-band { position: absolute; left: 0; top: 396px; width: 309px; height: 300px; }

  .store-info { position: absolute; top: 575px; width: 100%; text-align: center; color: var(--cream); }
  .store-info .brand-name { font-size: 20px; }
  .address {
    margin-top: 20px; font-family: "Josefin Sans", sans-serif; font-size: 7.5px;
    letter-spacing: 0.8px; line-height: 12px;
  }
  .website { margin-top: 14px; font-family: "Josefin Sans", sans-serif; font-size: 8px; letter-spacing: 0.4px; }

  .social-strip {
    position: absolute; left: 0; bottom: 0; width: 100%; height: 32px; background: var(--strip-teal);
    display: flex; justify-content: space-around; align-items: center; padding: 0 6px;
  }
  .handle {
    display: flex; align-items: center; gap: 3px; font-family: "Josefin Sans", sans-serif;
    font-size: 8.5px; color: var(--cream);
  }
  .handle-dot { width: 10px; height: 10px; border-radius: 50%; background: var(--navy); }
</style>
</head>
<body>
<main class="canvas">
  <section class="label">
    <div class="brand-block"><span class="brand-name">Harbor<br>Pantry</span></div>

    <p class="tagline">THE MIDWEST'S SOURCE OF<br>SEAFOOD &amp; PRODUCE<br>FOR OVER 15 YEARS</p>

    <div class="rule" style="top:201px"></div>
    <div class="rule-v" style="left:59px"></div>
    <div class="rule-v" style="left:256px"></div>

    <span class="side-note" style="left:36px">#1 SASHIMI GRADE</span>
    <span class="side-note" style="left:280px">WILD CAUGHT</span>

    <h1 class="product-title">YELLOWFIN<br>TUNA</h1>
    <p class="product-script">fresh Seafood</p>

    <div class="rule" style="top:343px"></div>
    <p class="claim">SOME OF THE BEST TUNA YOU CAN EAT</p>
    <div class="rule" style="top:360px"></div>
    <p class="pricing">PRICED PER POUND</p>
    <div class="rule" style="top:377px"></div>

    <svg class="sea-band" viewBox="0 0 309 300" role="img" aria-label="Wavy line pattern with an engraved tuna illustration">
      <path fill="#3e8790" d="M0 6 q7.7 -6 15.45 0 t15.45 0 t15.45 0 t15.45 0 t15.45 0 t15.45 0 t15.45 0 t15.45 0 t15.45 0 t15.45 0 t15.45 0 t15.45 0 t15.45 0 t15.45 0 t15.45 0 t15.45 0 t15.45 0 t15.45 0 t15.45 0 t15.45 0 V300 H0 Z"/>
      <ellipse cx="153" cy="74" rx="34" ry="15" fill="#3a7c86" transform="rotate(-18 153 74)"/>
    </svg>

    <div class="store-info">
      <span class="brand-name">Harbor Pantry</span>
      <p class="address">118 W. LAKEVIEW AVE<br>MILFORD, IL 60999<br>555-014-2290</p>
      <p class="website">www.harborpantry.com/</p>
    </div>

    <div class="social-strip">
      <span class="handle"><span class="handle-dot"></span>harbor_pantry</span>
      <span class="handle"><span class="handle-dot"></span>@harborpantry</span>
      <span class="handle"><span class="handle-dot"></span>@harborpantry</span>
    </div>
  </section>
</main>
</body>
</html>
```